Velmora Freightway Solutions Business cards

Would like a very unique design catchy but professional for business cards. Please use log provided.Marlon WellsCeo and Founder TransCon Logistix Solutions1-888-913-3225mwells@tlsolutionsus.comwww.tlsolutionsus.com

```html
<!DOCTYPE html>
<html lang="en">
<head>
<meta charset="utf-8">
<title>Velmora Freightway Solutions — Business Cards</title>
<link rel="stylesheet" href="https://fonts.googleapis.com/css2?family=Open+Sans:wght@400;600;700&display=swap">
<style>
  :root {
    --backdrop: #1f2023;
    --card: #ffffff;
    --brand-blue: #1672bd;
    --brand-red: #e4202a;
    --navy: #0c2340;
    --ink-white: #ffffff;
    --rule-blue: #1672bd;
  }
  * { box-sizing: border-box; margin: 0; padding: 0; }
  html, body {
    width: 1200px; height: 960px; overflow: hidden;
    background: var(--backdrop);
    font-family: "Open Sans", Arial, sans-serif;
  }
  .stage {
    position: relative; width: 1200px; height: 960px;
  }
  .card {
    position: absolute; left: 320px;
    width: 560px; height: 320px;
    background: var(--card);
    overflow: hidden;
  }
  .card--front { top: 110px; }
  .card--back { top: 530px; }

  /* Front */
  .front-mark {
    position: absolute; left: 0; right: 0; top: 96px;
    display: flex; align-items: center; justify-content: center; gap: 14px;
  }
  .front-mark__square {
    width: 26px; height: 26px; background: var(--brand-red);
  }
  .front-mark__name {
    font-weight: 700; font-size: 34px; letter-spacing: 0.5px;
    color: var(--brand-blue); line-height: 1.1; text-align: left;
  }
  .front-web {
    position: absolute; left: 60px; right: 60px; top: 222px;
    display: flex; align-items: center; gap: 14px;
  }
  .front-web__rule { flex: 1; height: 2px; background: var(--rule-blue); }
  .front-web__url {
    font-size: 14px; font-weight: 600; letter-spacing: 2px; color: #333a44;
  }

  /* Back */
  .back-mark {
    position: absolute; left: 34px; top: 30px;
    display: flex; align-items: center; gap: 8px;
  }
  .back-mark__square { width: 14px; height: 14px; background: var(--brand-red); }
  .back-mark__name {
    font-weight: 700; font-size: 17px; color: var(--brand-blue); letter-spacing: 0.5px;
  }
  .holder { position: absolute; left: 34px; top: 78px; }
  .holder__name {
    font-weight: 600; font-size: 18px; color: var(--brand-blue); letter-spacing: 0.3px;
  }
  .holder__title {
    font-size: 13px; color: var(--brand-red); letter-spacing: 0.3px; margin-top: 2px;
  }
  .wave { position: absolute; left: 0; top: 0; }
  .contacts {
    position: absolute; right: 22px; top: 206px;
    list-style: none; text-align: right;
    color: var(--ink-white); font-size: 13.5px; line-height: 22px;
  }
  .contacts li { display: flex; justify-content: flex-end; align-items: center; gap: 7px; }
  .contacts svg { width: 12px; height: 12px; flex: none; }
  .contacts .no-icon { padding-right: 0; }
</style>
</head>
<body>
<main class="stage">

  <section class="card card--front" aria-label="Card front">
    <div class="front-mark">
      <span class="front-mark__square"></span>
      <span class="front-mark__name">Velmora Freightway<br>Solutions</span>
    </div>
    <div class="front-web">
      <span class="front-web__rule"></span>
      <span class="front-web__url">www.vfwayroutes.com</span>
      <span class="front-web__rule"></span>
    </div>
  </section>

  <section class="card card--back" aria-label="Card back">
    <svg class="wave" width="560" height="320" viewBox="0 0 560 320" aria-hidden="true">
      <path d="M0,150 C140,185 320,222 560,188 L560,212 C320,246 140,212 0,176 Z" fill="#0c2340"/>
      <path d="M0,176 C140,212 320,246 560,212 L560,320 L0,320 Z" fill="#1672bd"/>
      <path d="M0,190 C160,222 330,250 560,226" fill="none" stroke="#ffffff" stroke-width="1.5" opacity="0.8"/>
    </svg>

    <div class="back-mark">
      <span class="back-mark__square"></span>
      <span class="back-mark__name">Velmora Freightway Solutions</span>
    </div>

    <div class="holder">
      <p class="holder__name">DORIAN PIKE</p>
      <p class="holder__title">CEO AND FOUNDER</p>
    </div>

    <ul class="contacts">
      <li>1-888-470-6158
        <svg viewBox="0 0 24 24" aria-hidden="true"><path fill="#fff" d="M6.6 10.8a15 15 0 0 0 6.6 6.6l2.2-2.2a1 1 0 0 1 1-.25 11.4 11.4 0 0 0 3.6.57 1 1 0 0 1 1 1V20a1 1 0 0 1-1 1A17 17 0 0 1 3 4a1 1 0 0 1 1-1h3.5a1 1 0 0 1 1 1c0 1.25.2 2.45.57 3.6a1 1 0 0 1-.25 1z"/></svg>
      </li>
      <li>dpike@vfwayroutes.com
        <svg viewBox="0 0 24 24" aria-hidden="true"><rect x="2" y="5" width="20" height="14" rx="2" fill="#fff"/><path d="M3 6l9 7 9-7" fill="none" stroke="#1672bd" stroke-width="2"/></svg>
      </li>
      <li>www.vfwayroutes.com
        <svg viewBox="0 0 24 24" aria-hidden="true"><circle cx="12" cy="12" r="9" fill="none" stroke="#fff" stroke-width="2"/><path d="M3 12h18M12 3c3 3 3 15 0 18M12 3c-3 3-3 15 0 18" fill="none" stroke="#fff" stroke-width="1.6"/></svg>
      </li>
      <li class="no-icon">2471 Harrow Mill Rd, Atlanta, GA 30327</li>
    </ul>
  </section>

</main>
</body>
</html>
```